Letterhead for a German Distribution/Manufacturing Company

We need a professional Letterhead in a unique Design.
not to playful.
The Letterhead has to show show that we are a international company with headquater in Germany.
all details like adress, Vat Tax Number, Bank Accout, Eori, email, Company number has to be on the Letterhead.
for example use: VAT TAX DE5470318 Bank Account: Kestrel Bank IBAN DE412058731ß204683 Swift: MORV0417352 EORI 3150428697 Company Number: HRB 51806 Adress: VOLMINTA UG Ahornweg 7 Postal Code 06384 City Burgstädt Country: Germany Email: info@volminta-example.com
the design can be colored but doesnt have to be
Industry/Entity Type
Manufacturing and international distribution
Requirements
Must have
- show that we are a international company with headquater in Germany. our company infos and logo

```html
<!DOCTYPE html>
<html lang="en">
<head>
<meta charset="utf-8">
<title>Volminta Letterhead</title>
<link rel="stylesheet" href="https://fonts.googleapis.com/css2?family=Arimo:wght@400;700&family=Didact+Gothic&family=Questrial&display=swap">
<style>
  :root {
    --backdrop: #cccacb;
    --paper: #ffffff;
    --ink: #4a4a4a;
    --ink-strong: #444444;
    --band-dark: #4a4a4a;
    --band-light: #a9a9a9;
    --signature-tone: #d9d9d9;
  }
  * { margin: 0; padding: 0; box-sizing: border-box; }
  html, body {
    width: 1173px; height: 1200px; overflow: hidden;
    background: var(--backdrop);
  }
  .letterhead {
    position: absolute; left: 230px; top: 96px;
    width: 713px; height: 1009px;
    background: var(--paper);
    color: var(--ink);
    font-family: "Arimo", Arial, sans-serif;
  }
  .brand {
    position: absolute; left: 44px; top: 62px;
    display: flex; align-items: center; gap: 14px;
  }
  .brand-dot {
    width: 50px; height: 50px; border-radius: 50%;
    background: var(--ink);
  }
  .brand-name {
    font-family: "Arimo", Arial, sans-serif;
    font-weight: 700; font-size: 40px; letter-spacing: 0.5px;
    color: var(--ink);
  }
  .company-details {
    position: absolute; right: calc(713px - 524px); top: 44px;
    text-align: right; font-size: 11px; line-height: 14.2px;
    white-space: nowrap;
  }
  .company-details b { color: var(--ink-strong); font-weight: 700; }
  .header-divider {
    position: absolute; left: 537px; top: 47px;
    width: 1px; height: 83px; background: var(--ink);
  }
  .contact {
    position: absolute; left: 552px; top: 42px;
    font-size: 11px; line-height: 14.2px; white-space: nowrap;
  }
  .contact-lines { list-style: none; margin-top: 2px; }
  .contact-lines li { display: flex; align-items: center; gap: 5px; }
  .contact-lines svg { width: 9px; height: 9px; fill: var(--ink); flex: none; }
  .greeting {
    position: absolute; left: 65px; top: 310px;
    font-family: "Questrial", "Didact Gothic", sans-serif;
    font-weight: 700; font-size: 16px; color: var(--ink-strong);
    -webkit-text-stroke: 0.3px var(--ink-strong);
  }
  .letter-body {
    position: absolute; left: 63px; top: 356px; width: 590px;
    font-size: 11.6px; line-height: 14.8px; white-space: nowrap;
  }
  .letter-body p + p { margin-top: 12.3px; }
  .closing {
    position: absolute; left: 65px; top: 660px;
    font-family: "Questrial", "Didact Gothic", sans-serif;
    font-size: 9.5px; font-weight: 700; color: var(--ink-strong);
    -webkit-text-stroke: 0.2px var(--ink-strong);
  }
  .signature {
    position: absolute; left: 65px; top: 703px;
    width: 116px; height: 36px; background: var(--signature-tone);
  }
  .footer-band {
    position: absolute; left: 0; bottom: 0; width: 713px; height: 15px;
  }
</style>
</head>
<body>
  <main class="letterhead">
    <header>
      <div class="brand">
        <span class="brand-dot"></span>
        <span class="brand-name">VOLMINTA</span>
      </div>
      <div class="company-details">
        <div><b>VAT TAX</b> DE5470318</div>
        <div><b>Bank Account:</b> Kestrel Bank</div>
        <div><b>IBAN</b> DE412058731ß204683</div>
        <div><b>Swift:</b> MORV0417352</div>
        <div><b>EORI</b> 3150428697</div>
        <div><b>Company Number:</b> HRB 51806</div>
      </div>
      <div class="header-divider"></div>
      <address class="contact" style="font-style:normal">
        <div>Ahornweg 7</div>
        <div>06384, Burgstädt</div>
        <div>Germany</div>
        <ul class="contact-lines">
          <li><svg viewBox="0 0 10 10" aria-hidden="true"><path d="M2 0.5 L3.6 2.6 L2.7 3.6 Q3.6 5.6 6.4 7.3 L7.4 6.4 L9.5 8 L8.2 9.5 Q4.5 9.2 1.5 5.5 Q0.2 3.2 0.6 1.6 Z"/></svg>123-456-7890</li>
          <li><svg viewBox="0 0 10 10" aria-hidden="true"><path d="M0.5 2 H9.5 V8.5 H0.5 Z M1.2 2.6 L5 5.6 L8.8 2.6" stroke="#fff" stroke-width="0.8"/></svg>info@volminta-example.com</li>
          <li><svg viewBox="0 0 10 10" aria-hidden="true"><circle cx="5" cy="5" r="4.6"/><path d="M5 0.8 V9.2 M0.8 5 H9.2" stroke="#fff" stroke-width="0.8"/></svg>www.volminta-example.com</li>
        </ul>
      </address>
    </header>

    <h1 class="greeting">Dear Mr. Smith,</h1>

    <section class="letter-body">
      <p>Lorem ipsum dolor sit amet, consectetuer adipiscing elit, sed diam nonmmy nibh euismod tincidunt ut laor<br>eet dolore magna aliquam erat volutpat. Ut wisi enim ad minim veniam, quis nostrud exerci tationmcorper<br>suscipit lobortis nisl ut aliquip ex ea commodo consequat. Duis autem vel eum iriure dolor in hendrerit in<br>vulputate velit esse molestie consequat, vel illum dolore eu feugiat</p>
      <p>Rorem ipsum dolor sit amet, consectetuer adipiscing elit, sed diam nonmmy nibh euismod tincidunt ut laor<br>eet dolore magna aliquam erat volutpat. Ut wisi enim ad minim veniam, quis nostrud exerci tationmcorper<br>suscipit lobortis nisl ut aliquip ex ea commodo consequat. Duis autem vel eum iriure dolor in hendrerit in<br>vulputate velit esse molest</p>
      <p>Dorem ipsum dolor sit amet, consectetuer adipiscing elit, sed diam nonmmy nibh euismod tincidunt ut laor<br>eet dolore magna aliquam erat volutpat. Ut wisi enim ad minim veniam, quis nostrud exerci tationmcorper<br>suscipit lobortis nisl ut aliquip ex ea commodo consequat. Duis autem vel eum iriure dolor in hendrerit in<br>suscipit lobortis nisl ut aliquip ex ea commodo consequat. Duis autem vel eum iriure dolor in hendrerit in<br>vulputate velit esse molestie consequat, vel illum</p>
      <p>Sorem ipsum dolor sit amet, consectetuer adipiscing elit, sed diam nonmmy nibh euismod tincidunt ut laor<br>eet dolore magna aliquam erat volutpat. Ut wisi enim ad minim veniam, quis nostrud exerci tationmcorper<br>suscipit lobortis nisl ut aliquip ex ea commodo consequat. Duis autem vel eum iriure dolor in</p>
    </section>

    <p class="closing">Sincerely,</p>
    <div class="signature" role="img" aria-label="Handwritten signature"></div>

    <svg class="footer-band" viewBox="0 0 713 15" preserveAspectRatio="none" aria-hidden="true">
      <polygon points="0,0 517,0 505,15 0,15" fill="var(--band-dark)"/>
      <polygon points="529,0 713,0 713,15 516,15" fill="var(--band-light)"/>
    </svg>
  </main>
</body>
</html>
```